Modern Business Card for Larkwell 2018

Our company assumes the best about people. We are creating an online community of entrepreneurs and business leaders who struggle with marketing their business online.

This business card should POP! We recently got a new logo and are launching a new website next month, so our business cards should make a statement that feels:
-Fresh
-Smart
-Trustworthy
-Fun

Target Market(s)

small business owners, entrepreneurs

Industry/Entity Type

Digital Marketing

Contact Information for Business Card

Dimensions: 3.5" x 2"

Font styles to use
Sans Serif

Colors
f37122
ffffff

Requirements
Must have
• We need a business card with a modern, bold design. We will use one side of the card as a lead-generation offer, so text on one side will need to fit up to 140 characters. The business card should stick to our core colors (orange, black, and white).
Nice to have
• We think a vertical "portrait" design could be interesting.
Should not have
• Should not look like a traditional business card. The round icon should stand out from a distance.

```html
<!DOCTYPE html>
<html lang="en">
<head>
<meta charset="utf-8">
<title>Larkwell Business Card</title>
<link href="https://fonts.googleapis.com/css2?family=Roboto:ital,wght@0,400;0,500;0,700;1,700&family=Yellowtail&display=swap" rel="stylesheet">
<style>
  :root {
    --orange: #f37122;
    --orange-deep: #ef6a26;
    --white: #ffffff;
    --paper: #f3f3f3;
    --ink: #2b2b2b;
    --charcoal: #262626;
    --backdrop: #e4e1dc;
  }
  * { margin: 0; padding: 0; box-sizing: border-box; }
  html, body { width: 1200px; height: 960px; overflow: hidden; }
  body {
    position: relative;
    background: var(--backdrop);
    font-family: "Roboto", Arial, sans-serif;
  }
  .card {
    position: absolute;
    width: 600px;
    height: 342px;
    border-radius: 18px;
    overflow: hidden;
  }
  /* Front */
  .card-front { left: 314px; top: 113px; background: var(--paper); }
  .front-mark {
    position: absolute; left: 42px; top: 104px;
    display: flex; flex-direction: column; align-items: center; gap: 10px;
    width: 140px;
  }
  .mark-dot { width: 56px; height: 56px; border-radius: 50%; background: var(--orange); }
  .front-mark .brand-name {
    font-weight: 700; font-size: 26px; letter-spacing: 1px; color: var(--orange);
  }
  .front-details {
    position: absolute; left: 290px; top: 114px; width: 260px;
    text-align: center;
  }
  .job-title { font-size: 15px; font-weight: 500; color: var(--ink); letter-spacing: 0.3px; }
  .person-name {
    font-family: "Yellowtail", cursive; font-size: 42px; color: var(--orange);
    line-height: 1; margin-top: 12px; text-transform: uppercase;
  }
  .email { font-size: 15px; font-weight: 500; color: #444; margin-top: 8px; }
  .front-band { position: absolute; left: 0; bottom: 0; width: 600px; height: 22px; }

  /* Back */
  .card-back { left: 311px; top: 472px; background: var(--orange-deep); border-radius: 20px; }
  .back-brand {
    position: absolute; left: 46px; top: 58px; width: 226px;
    display: flex; flex-direction: column; align-items: center;
    color: var(--white);
  }
  .back-brand .mark-dot { width: 36px; height: 36px; background: var(--white); }
  .back-brand .brand-name {
    font-weight: 700; font-size: 38px; letter-spacing: 1.5px; margin-top: 12px; line-height: 1;
  }
  .tagline {
    font-weight: 700; font-style: italic; font-size: 11.5px; letter-spacing: 0.6px;
    margin-top: 8px; text-transform: uppercase;
  }
  .divider {
    position: absolute; left: 297px; top: 25px; width: 1px; height: 166px;
    background: rgba(255,255,255,0.55);
  }
  .offer { position: absolute; left: 323px; top: 29px; width: 260px; color: var(--white); }
  .offer-headline { font-weight: 700; font-size: 18px; line-height: 21px; text-transform: uppercase; }
  .offer-body { font-size: 15px; line-height: 19px; margin-top: 7px; }
  .offer-url { font-weight: 700; font-size: 19.5px; margin-top: 10px; }
  .note-box {
    position: absolute; left: 20px; top: 217px; width: 557px; height: 101px;
    background: var(--white); border-radius: 18px;
  }
  .note-line { position: absolute; left: 24px; right: 28px; height: 1px; background: #333; }
  .note-line:first-child { top: 31px; }
  .note-line:last-child { top: 71px; }
</style>
</head>
<body>
  <section class="card card-front">
    <div class="front-mark">
      <span class="mark-dot"></span>
      <span class="brand-name">LARKWELL</span>
    </div>
    <div class="front-details">
      <p class="job-title">STORY MARKETING COACH</p>
      <p class="person-name">Dana Whitford</p>
      <p class="email">dana@larkwellhq.com</p>
    </div>
    <svg class="front-band" viewBox="0 0 600 22" aria-hidden="true">
      <polygon points="0,0 392,0 386,22 0,22" fill="var(--orange)"/>
      <polygon points="392,0 396,0 390,22 386,22" fill="var(--white)"/>
      <polygon points="396,0 600,0 600,22 390,22" fill="var(--charcoal)"/>
    </svg>
  </section>

  <section class="card card-back">
    <div class="back-brand">
      <span class="mark-dot"></span>
      <span class="brand-name">LARKWELL</span>
      <span class="tagline">Tell stories that inspire action</span>
    </div>
    <div class="divider"></div>
    <div class="offer">
      <p class="offer-headline">Reach more people.<br>Make more money.<br>Create more impact.</p>
      <p class="offer-body">Get your free Larkwell<br>Starter Package and our<br>marketing guide today at</p>
      <p class="offer-url">Larkwellhq.com/start</p>
    </div>
    <div class="note-box">
      <div class="note-line"></div>
      <div class="note-line"></div>
    </div>
  </section>
</body>
</html>
```